Newsletter Design for Travel - Group -Event Agency

We are looking for a standard Newsletter Design which we can use regularly to send out to a number of clients. The idea is to add 1 or more pictures and a promotion or program as well as some possible news. We are a travel agency and want to promote our products in either the travel sector (B2C) or event and group sector (B2B , see our company logo enclosed.

Target Market(s)

We have different target markets, but in the end it's always connected to the travel industry

Industry/Entity Type

Events

Font styles to use
Sans Serif

Colors
3176b5
eaf1f7

Requirements
Must have
• Area to upload picture(s), text field and business data (website, linkedin, facebook, instagram, tel and e-mail contacts. Subscribe/unsubscrive
Nice to have
• optional CTA Buttom, p.e. "make a virutal appointment" or similar
Should not have
• should stay with the colours of our logo / website - grey, a bit blue

```html
<!DOCTYPE html>
<html lang="en">
<head>
<meta charset="utf-8">
<title>Tejo Horizon Newsletter</title>
<link href="https://fonts.googleapis.com/css2?family=Montserrat:wght@700;800&family=Inter:wght@400;500&display=swap" rel="stylesheet">
<style>
:root{
  --blue:#2b64a9;
  --blue-line:#3176b5;
  --pale:#e4ecf5;
  --pale-box:#e8eff7;
  --ink:#1f2329;
  --text:#2e3238;
  --white:#ffffff;
  --field-border:#8c8f94;
}
*{margin:0;padding:0;box-sizing:border-box}
html,body{width:1200px;height:4156px;overflow:hidden;background:var(--white)}
body{position:relative;font-family:"Inter",Arial,sans-serif;color:var(--text)}
.abs{position:absolute}

/* hero */
.hero-photo{left:0;top:0;width:1200px;height:812px;
  background:linear-gradient(180deg,#c9ccd0 0%,#b9a69a 35%,#d4b59e 60%,#9d8f8c 85%,#6f6c73 100%)}
.hero-band{left:0;top:808px;width:1200px;height:14px;background:var(--blue)}
.brand{left:44px;top:44px;font-family:"Montserrat",Arial,sans-serif;font-weight:800;font-size:48px;color:var(--ink);letter-spacing:1px}
.body-bg{left:0;top:822px;width:1200px;height:2308px;background:var(--pale)}
.cta{left:236px;top:762px;width:730px;height:114px;background:var(--blue);border-radius:12px;
  color:var(--white);font-family:"Montserrat",Arial,sans-serif;font-weight:800;font-size:35px;
  display:flex;align-items:center;justify-content:center;letter-spacing:.5px}

/* section heading */
.section-title{left:0;width:1200px;display:flex;align-items:center;justify-content:center;gap:28px;
  font-family:"Montserrat",Arial,sans-serif;font-weight:800;font-size:46px;color:var(--ink)}
.section-title::before,.section-title::after{content:"";width:68px;height:5px;background:var(--blue)}

/* promo cards */
.promo-image{width:554px;height:284px;border-radius:8px}
.promo-title{width:554px;text-align:center;font-family:"Montserrat",Arial,sans-serif;font-weight:700;font-size:30px;color:var(--ink)}
.promo-text{width:554px;text-align:center;font-size:27px;line-height:35px;color:var(--text);white-space:nowrap}

/* news */
.news-feature{left:28px;top:2248px;width:1136px;height:314px;background:var(--blue);border-radius:8px;padding:62px 64px;color:var(--white)}
.news-feature h2{font-family:"Montserrat",Arial,sans-serif;font-weight:800;font-size:34px;margin-bottom:20px}
.news-feature p{font-size:29px;line-height:42px;white-space:nowrap}
.news-list{left:28px;top:2610px;width:1136px;height:462px;border:2px solid var(--blue-line);border-radius:8px;background:var(--pale-box)}
.news-icon{width:128px;height:128px;border-radius:50%;background:var(--blue);display:flex;align-items:center;justify-content:center}
.news-item-title{left:220px;font-family:"Montserrat",Arial,sans-serif;font-weight:800;font-size:31px;color:var(--ink)}
.news-item-text{left:220px;width:860px;font-size:27px;line-height:40px;color:var(--text);white-space:nowrap}

/* form */
.field{width:524px;height:104px;border:2px solid var(--field-border);border-radius:6px;background:var(--white);
  font-size:28px;color:var(--ink);display:flex;align-items:center;justify-content:space-between;padding:0 34px}
.submit{left:52px;top:3474px;width:1082px;height:104px;background:var(--blue);border-radius:6px;color:var(--white);
  font-family:"Montserrat",Arial,sans-serif;font-weight:800;font-size:40px;display:flex;align-items:center;justify-content:center;letter-spacing:1px}

/* footer */
.footer{left:0;top:3656px;width:1200px;height:500px;background:var(--blue)}
.footer-rule{left:0;top:3886px;width:1200px;height:3px;background:#3a72b8}
.contact-icon{width:78px;height:78px;border-radius:50%;background:var(--white);display:flex;align-items:center;justify-content:center}
.contact-label{font-size:29px;color:var(--white);letter-spacing:.5px}
.contact-value{font-size:38px;color:var(--white)}
.social{top:3956px;width:60px;height:60px;border-radius:50%;background:var(--white)}
.footer-links{left:0;top:4064px;width:1200px;text-align:center;font-size:28px;color:var(--white);word-spacing:4px}
</style>
</head>
<body>

<header>
  <div class="abs hero-photo" role="img" aria-label="Hand holding a cloud with famous world landmarks on it"></div>
  <div class="abs brand">Tejo Horizon</div>
  <div class="abs hero-band"></div>
</header>

<main>
  <div class="abs body-bg"></div>
  <a class="abs cta">MAKE A VIRUTAL APPOINTMENT</a>

  <h2 class="abs section-title" style="top:976px">PROMOTION</h2>

  <div class="abs promo-image" style="left:28px;top:1098px;background:linear-gradient(135deg,#d8d8d4,#8fb3b8 45%,#c9b4a0)" role="img" aria-label="Laptop showing a travel booking page"></div>
  <div class="abs promo-image" style="left:612px;top:1098px;background:linear-gradient(135deg,#3a3c40,#6d6f73 50%,#c09a78)" role="img" aria-label="Travel agent advising a couple in front of a world map"></div>
  <div class="abs promo-image" style="left:28px;top:1590px;background:linear-gradient(135deg,#5e9ac9,#c8cdd6 50%,#7a8ea8)" role="img" aria-label="Smiling traveller holding a passport and tickets"></div>
  <div class="abs promo-image" style="left:612px;top:1590px;background:linear-gradient(180deg,#3a8ad8,#9ccbee 45%,#6f8f6a 75%,#2f6f9a)" role="img" aria-label="World landmarks gathered on a globe under blue sky"></div>

  <div class="abs promo-title" style="left:28px;top:1420px">LOREM IPSUM</div>
  <p class="abs promo-text" style="left:28px;top:1476px">It is a long established fact that a<br>reader will be distracted by.</p>
  <div class="abs promo-title" style="left:612px;top:1420px">LOREM IPSUM</div>
  <p class="abs promo-text" style="left:612px;top:1476px">It is a long established fact that a<br>reader will be distracted by.</p>
  <div class="abs promo-title" style="left:28px;top:1912px">LOREM IPSUM</div>
  <p class="abs promo-text" style="left:28px;top:1968px">It is a long established fact that a<br>reader will be distracted by.</p>
  <div class="abs promo-title" style="left:612px;top:1912px">LOREM IPSUM</div>
  <p class="abs promo-text" style="left:612px;top:1968px">It is a long established fact that a<br>reader will be distracted by.</p>

  <h2 class="abs section-title" style="top:2140px">NEWS</h2>

  <article class="abs news-feature">
    <h2>LOREM IPSUM IS SIMPLY DUMMY TEXT</h2>
    <p>There are many variations of passages of Lorem Ipsum available,<br>but the majority have suffered alteration in some form, by injected<br>humour, or randomised words which don't look even.</p>
  </article>

  <section class="abs news-list">
    <div class="abs news-icon" style="left:48px;top:62px">
      <svg width="76" height="64" viewBox="0 0 76 64"><rect x="4" y="14" width="68" height="46" rx="7" fill="#fff"/><rect x="26" y="4" width="24" height="12" rx="3" fill="none" stroke="#fff" stroke-width="5"/><rect x="4" y="30" width="68" height="4" fill="#2b64a9"/><rect x="32" y="26" width="12" height="12" rx="2" fill="#fff" stroke="#2b64a9" stroke-width="3"/></svg>
    </div>
    <div class="abs news-item-title" style="top:56px">IT IS A LONG ESTABLISHED FACT</div>
    <p class="abs news-item-text" style="top:108px">There are many variations of passages of Lorem Ipsum<br>available, but the majority have suffered alteration.</p>

    <div class="abs news-icon" style="left:48px;top:274px">
      <svg width="76" height="70" viewBox="0 0 76 70"><rect x="4" y="6" width="56" height="40" rx="3" fill="none" stroke="#fff" stroke-width="5"/><rect x="26" y="46" width="12" height="10" fill="#fff"/><rect x="16" y="56" width="32" height="5" fill="#fff"/><polyline points="12,36 24,24 32,30" fill="none" stroke="#fff" stroke-width="4"/><circle cx="48" cy="26" r="14" fill="#2b64a9" stroke="#fff" stroke-width="5"/><line x1="58" y1="36" x2="70" y2="48" stroke="#fff" stroke-width="6" stroke-linecap="round"/></svg>
    </div>
    <div class="abs news-item-title" style="top:268px">LOREM IPSUM IS SIMPLY DUMMY</div>
    <p class="abs news-item-text" style="top:320px">There are many variations of passages of Lorem Ipsum<br>available, but the majority have suffered alteration.</p>
  </section>

  <form>
    <div class="abs field" style="left:54px;top:3196px">Name</div>
    <div class="abs field" style="left:610px;top:3196px">Email</div>
    <div class="abs field" style="left:54px;top:3330px">Phone</div>
    <div class="abs field" style="left:610px;top:3330px">Upload Images
      <svg width="36" height="36" viewBox="0 0 36 36"><path d="M18 4 L8 15 H14 V24 H22 V15 H28 Z" fill="#2b64a9"/><path d="M3 24 V32 H33 V24" fill="none" stroke="#2b64a9" stroke-width="4"/></svg>
    </div>
    <div class="abs submit">SUBMIT</div>
  </form>
</main>

<footer>
  <div class="abs footer"></div>
  <div class="abs contact-icon" style="left:50px;top:3740px">
    <svg width="40" height="40" viewBox="0 0 24 24"><path d="M6.6 10.8c1.4 2.8 3.8 5.1 6.6 6.6l2.2-2.2c.3-.3.7-.4 1-.2 1.1.4 2.3.6 3.6.6.6 0 1 .4 1 1V20c0 .6-.4 1-1 1C10.6 21 3 13.4 3 4c0-.6.4-1 1-1h3.5c.6 0 1 .4 1 1 0 1.3.2 2.5.6 3.6.1.3 0 .7-.2 1z" fill="#2b64a9"/></svg>
  </div>
  <div class="abs contact-label" style="left:158px;top:3728px">CALL US</div>
  <div class="abs contact-value" style="left:158px;top:3768px">555.010.2040</div>

  <div class="abs contact-icon" style="left:548px;top:3740px">
    <svg width="36" height="28" viewBox="0 0 36 28"><rect x="2" y="2" width="32" height="24" rx="3" fill="#2b64a9"/><polyline points="4,5 18,16 32,5" fill="none" stroke="#fff" stroke-width="3"/></svg>
  </div>
  <div class="abs contact-label" style="left:656px;top:3728px">EMAIL US</div>
  <div class="abs contact-value" style="left:656px;top:3768px">info@TejoHorizon.com</div>

  <div class="abs footer-rule"></div>
  <a class="abs social" style="left:482px" aria-label="Social profile one"></a>
  <a class="abs social" style="left:560px" aria-label="Social profile two"></a>
  <a class="abs social" style="left:634px" aria-label="Social profile three"></a>
  <p class="abs footer-links">Subscribe &nbsp;/&nbsp; Unsubscribe</p>
</footer>

</body>
</html>
```